Business Card for Industrial Distributor

We need a business card design for an industrial distributor. We sell machine parts for the manufacturing and oil industry. We would like the cards to look clean and modern but with a touch of industry.

Our colors are blue/white.

Please feel free to visit our website www.korvelpartsco.com

Target Market(s)

mexican manufacturers in the automobile/aerospace industry

Industry/Entity Type

Industrial

Colors
ffffff
0555a3

```html
<!DOCTYPE html>
<html lang="en">
<head>
<meta charset="utf-8">
<title>Korvel International Corp. – Business Card</title>
<link rel="stylesheet" href="https://fonts.googleapis.com/css2?family=Open+Sans:wght@400;600;700;800&display=swap">
<style>
  :root {
    --brand-blue: #2f45b8;
    --brand-blue-deep: #23379e;
    --brand-blue-light: #3d58c9;
    --card-white: #ffffff;
    --card-grey: #c9c9cc;
    --card-grey-soft: #ececee;
    --stage: #e6e7ea;
    --ink-white: #ffffff;
  }
  * { box-sizing: border-box; margin: 0; padding: 0; }
  html, body {
    width: 1200px; height: 780px; overflow: hidden;
    background: var(--stage);
    font-family: "Open Sans", Arial, sans-serif;
  }
  .canvas { position: relative; width: 1200px; height: 780px; }
  .card {
    position: absolute; top: 240px;
    width: 520px; height: 300px;
    border-radius: 18px; overflow: hidden;
    box-shadow: 0 10px 28px rgba(20, 30, 70, 0.18);
  }
  .card--front { left: 50px; background: var(--card-white); }
  .card--back {
    left: 630px;
    background: radial-gradient(ellipse at 40% 35%, var(--brand-blue-light), var(--brand-blue-deep) 90%);
  }
  .front-wave { position: absolute; inset: 0; }

  .brand {
    position: absolute; left: 30px; top: 34px;
    display: flex; align-items: center; gap: 12px;
  }
  .brand__dot {
    width: 48px; height: 48px; border-radius: 50%;
    background: var(--brand-blue);
  }
  .brand__name {
    font-weight: 800; font-size: 52px; line-height: 1;
    color: var(--brand-blue); letter-spacing: -1px;
  }

  .contact {
    position: absolute; left: 34px; bottom: 20px;
    color: var(--ink-white);
  }
  .contact__person { font-size: 16px; font-weight: 700; letter-spacing: 0.5px; line-height: 22px; }
  .contact__role { font-weight: 400; font-size: 13px; opacity: 0.85; }
  .contact__role::before { content: "|"; margin: 0 8px; opacity: 0.6; }
  .contact__line {
    display: flex; align-items: center; gap: 8px;
    font-size: 13px; line-height: 20px;
  }
  .contact__icon { width: 13px; height: 13px; flex: none; }

  .company {
    position: absolute; right: 28px; bottom: 108px;
    text-align: right; color: var(--ink-white);
  }
  .company__name { font-size: 15px; font-weight: 700; line-height: 21px; }
  .company__address { font-size: 12px; line-height: 18px; opacity: 0.92; }

  .back__name {
    position: absolute; left: 0; right: 0; top: 82px;
    text-align: center;
    font-weight: 800; font-size: 88px; line-height: 1;
    color: var(--ink-white); letter-spacing: -1px;
  }
  .back__web {
    position: absolute; left: 0; right: 0; top: 200px;
    display: flex; align-items: center; justify-content: center; gap: 18px;
    color: var(--ink-white); font-size: 14px; letter-spacing: 0.3px;
  }
  .back__rule { width: 80px; height: 1px; background: rgba(255,255,255,0.55); }
</style>
</head>
<body>
<main class="canvas">

  <section class="card card--front" aria-label="Card front">
    <svg class="front-wave" viewBox="0 0 520 300" width="520" height="300" aria-hidden="true">
      <path d="M0 0 H520 V300 H0 Z" fill="var(--card-white)"/>
      <path d="M0 166 C200 166 330 46 520 36 V300 H0 Z" fill="var(--card-grey-soft)"/>
      <path d="M0 178 C200 178 330 58 520 48 V300 H0 Z" fill="var(--card-grey)"/>
      <path d="M0 190 C200 190 330 70 520 60 V300 H0 Z" fill="var(--brand-blue)"/>
    </svg>

    <div class="brand">
      <span class="brand__dot"></span>
      <span class="brand__name">Korvel</span>
    </div>

    <div class="company">
      <p class="company__name">Korvel International Corp.</p>
      <p class="company__address">4820 Harbor Line Rd.</p>
      <p class="company__address">Eastbrook, TX 78599</p>
    </div>

    <div class="contact">
      <p class="contact__person">DANIEL REYES<span class="contact__role">Manager</span></p>
      <p class="contact__line">
        <svg class="contact__icon" viewBox="0 0 14 14" aria-hidden="true"><rect x="0.5" y="0.5" width="13" height="13" rx="2" fill="none" stroke="#fff"/><path d="M4 3h2l1 2.5-1.2.8a5 5 0 0 0 2 2l.8-1.2L11 8v2a1 1 0 0 1-1 1A7 7 0 0 1 3 4a1 1 0 0 1 1-1z" fill="#fff"/></svg>
        (956) 555 - 0142
      </p>
      <p class="contact__line">
        <svg class="contact__icon" viewBox="0 0 14 14" aria-hidden="true"><rect x="0.5" y="0.5" width="13" height="13" rx="2" fill="none" stroke="#fff"/><rect x="4" y="2.5" width="6" height="9" rx="1" fill="#fff"/></svg>
        (956) 555 - 0187
      </p>
      <p class="contact__line">
        <svg class="contact__icon" viewBox="0 0 14 14" aria-hidden="true"><rect x="0.5" y="0.5" width="13" height="13" rx="2" fill="none" stroke="#fff"/><rect x="2.5" y="4" width="9" height="6" fill="none" stroke="#fff"/><path d="M2.5 4l4.5 3.5L11.5 4" fill="none" stroke="#fff"/></svg>
        sales@korvelpartsco.com
      </p>
    </div>
  </section>

  <section class="card card--back" aria-label="Card back">
    <p class="back__name">Korvel</p>
    <p class="back__web">
      <span class="back__rule"></span>
      www.korvelpartsco.com
      <span class="back__rule"></span>
    </p>
  </section>

</main>
</body>
</html>
```